Nutritional & Gastrointestinal Health Consulting Service-Website design

We need a website design for a new health consulting service called "Bright Vale" based in Perth, Australia.

We will be providing consulting services in the areas of:
1) Nutrition and Diet
2) Gastrointestinal Health (which means stomach & digestive system related health)

These consulting services will be provided by an Accredited Dietitian and a Paediatric Gastroenterologist.

We are open to creative ideas in terms of design, layout, fonts and colours. We also would love to see images of nature in the backdrop with families (adults with kids) having a good time, fresh fruits and vegetables displayed in a farmer's market or supermarket. 2 or 3 images should be sufficient. We would also definitely want our logo somewhere in the main page of website. The logo file is also attached. Please have a look at a website's design that we really liked. We would love to see designs inspired by that style. The website details are in the in the "nice to have priorities" section of this project brief.

We also would be looking at website designers with software coding skills so that if we like the design we can go ahead with the next step of coding.

The website design should communicate the purpose of the website and at the same time be simple, elegant and unique/eye-catching.

We look forward to receiving creative ideas for our website from you all. Good luck!

More details have been added to our project- for example: Logo, fonts style, must haves etc etc. Please view the updated project brief. Looking forward to receiving your fantastic ideas for our website. Thanking you

Hi, I have updated the colour preference. Will add the content preferences tomorrow. thanks

Hello all, I have now added a LOT more content to what we want in our website. It is very much in detail, so please carefully have a read through the entire project brief. If you have any questions write back to me and I will try to respond as quickly as I can. Last few days were busy so couldn't respond quickly to all of you who had send me designs/queries/questions. Thank you for your patience. I look forward to receiving fantastic designs from you all. Good Luck :-)

Target Market(s)

Adults based in western speaking countries aged 18 to 60 years

Industry/Entity Type

Software

Font styles to use
Sans Serif
Script

Colors
faa54b
acd036

Requirements
Must have
• The website must have the MAIN logo file attached. I have attached 3 files: 1) MAIN logo; 2) supplementary logo A ; 3) supplementary logo B

I have selected 2 colours from the colour scheme (see below)-(as the colour of our logo is that).
However we would also like to see LIGHT CHOCOLATE BROWN or CHOCOLATE BROWN colour used as the background colour of the website
Preferred WEBSITE CONTENT:
1) HOME PAGE:
Content required=
--Company Logo
--Dr Dorian Pelham
Paediatric Gastroenterologist & Hepatologist
-Marla Pelham.
Dietitian & Nutritionist
--Website Menu (either listed horizontally or vertically):
Once clicked on each name:

Under each of the Website Menu items we want the following Headings to be added

2) ABOUT US page:
Sub-heading under this: Qualification, Skills, Special Interest

3) SERVICES
DORIAN'S PAGE: Individual Consultation, Endoscopy procedures
Individual Consultation, Group Based Services, Food Diary, Food & Symptom Diary

4) FEES & REBATE: Content as below:
Please Note: Payment of full fees is required at the time of consultation and procedures. 48 hours notice is required for cancellation of appointments/non-attendance. Failure to provide this may result in a fee being incurred. Please call reception to find out the amount of fee charged for cancellation of appointments/non-attendance.
headings are:
Paediatric Gastroenterology:
Dorian's pge
Individual Consultation - Initial (upto 30 mins):
Review Consultation (upto 15 mins):
Endoscopy procedures - No Gap fees charged. Fees will be billed directly to Vitacover. If any queries, please contact reception.

marla's pge
sub heading:
Individual Consultation - Initial (upto 45 mins):
Individual Consultation - Review (upto 30 mins):

Concession-Individual Consultation -Initial (upto 45 mins):
Concession-Individual Consultation - Review (upto 30 mins):
Please Note: Concession applies for health care card holders & pensioners

Group Based Services: Pricing subject to the type of service provided. Please contact us for an obligation free quote.
Education Topics Include:
- Paediatric Nutrition (Introducing Solids, Fussy Eating, Healthy Eating)
- Pregnancy Nutrition, Gestational Diabetes, Breastfeeding/Lactation Nutrition
- Healthy Eating, Supermarket Shopping Tips, Nutrition Label Reading Tips, Healthier
sub heading under nutrition & diet:
-Vitacover:
--A rebate of $52.95 is available from Vitacover if an EPC ( Enhanced Primary Care)/Chronic Disease Management (CDM) plan is issued by your GP.
--All mandatory paperwork needs to be available at the time of making your appointment for your eligibility.
-Private Health Fund:
--Most private health funds provide rebate on dietetic appointments. However the rebate amount depends on your level of cover. Thus, please contact your health fund to determine your entitled rebate.
-RSB: Approved provider for RSB services

6) FOR DOCTORS: Bright Vale Paediatric Gastroenterologist Referral Form
Bright Vale Dietitian Referral form
7) LOCATIONS & CONTACT

Paediatric Gastroenterology & Hepatology Service
Suite 46
Holy Lantern Bramcote Medical Centre
17 Colin Ferris Pde,
MURDOCH, WA 6150
P: (08) 9422 5061
F: (08) 9422 3094

Nutrition & Diet Service
Suite 46
17 Colin Ferris Pde,
MURDOCH, WA 6150
P: (08) 9422 5061
F: (08) 9422 3094

Tolland Medical Centre
58-60 Karrigan Parkway,
MANDURAH, WA 6210
P: (08) 9647 2283
F: (08) 96724419
www.tmcexample.com.au

This page should have a webform that has following titles:
-Your Name
-Your Email
-Your Phone
-Message

8) NEWS & BLOG
Nice to have
• We liked the design style of the websites below:
https://www.vendoraplex.example/

http://qoravelt.example/

But feel free to use your creativity too
Should not have
• Please do not use any body building or muscle building images

```html
<!DOCTYPE html>
<html lang="en">
<head>
<meta charset="utf-8">
<title>Bright Vale – Nutrition &amp; Diet</title>
<link rel="stylesheet" href="https://fonts.googleapis.com/css2?family=Arimo:wght@400;700&display=swap">
<style>
:root{
  --choc-dark:#5a3319;
  --choc:#7b5b47;
  --page:#bcab9d;
  --content:#ddd3cc;
  --frame:#f4f1ee;
  --title:#5b2d12;
  --link-orange:#faa54b;
  --link-green:#d9ef3c;
  --link-pale:#eef08c;
  --utility:#6e4526;
  --ink:#111;
}
*{box-sizing:border-box;margin:0;padding:0}
html,body{width:1200px;height:833px;overflow:hidden}
body{font-family:"Arimo",Arial,sans-serif;color:var(--ink);position:relative;background:var(--choc-dark)}
.backdrop{position:absolute;inset:0;background:radial-gradient(circle at 50% 40%,#6a4226,var(--choc-dark) 70%)}
.sheet{position:absolute;left:35px;top:37px;width:1130px;height:758px;border:2px solid var(--frame);border-radius:14px;
  background:linear-gradient(180deg,#c2b2a5,#b6a394)}
.utility{position:absolute;right:42px;top:8px;font-size:13px}
.utility a{color:var(--utility)}
.utility .sep{color:#fff;margin:0 7px}
.masthead{position:absolute;left:213px;top:23px;width:700px;height:178px;background:var(--choc);border:3px solid var(--frame);border-radius:18px;
  display:flex;align-items:flex-end;justify-content:center;padding-bottom:38px;gap:10px}
.brand-mark{width:34px;height:34px;border-radius:50%;background:var(--link-orange)}
.brand-name{font-size:32px;font-weight:700;color:#acd036;letter-spacing:1px}
.box{position:absolute;border:3px solid var(--frame);border-radius:8px;background:var(--choc)}
.box h2{height:27px;border-bottom:3px solid var(--frame);text-align:center;color:#fff;font-size:14px;line-height:26px}
.main-menu{left:25px;top:219px;width:224px;height:242px}
.main-menu ul{margin:22px 0 0 56px;font-size:12.5px;font-weight:700;line-height:17.5px;color:#fff}
.main-menu li{margin-left:2px}
.main-menu a{color:var(--link-green)}
.main-menu a.warm{color:var(--link-orange)}
.user-login{left:879px;top:219px;width:223px;height:212px}
.user-login form{padding:17px 0 0 15px;color:#fff;font-size:13px;font-weight:700}
.user-login label{display:block}
.user-login .req{color:#e0302a}
.user-login input{width:108px;height:21px;border:1px solid #888;margin:1px 0 15px;font:13px "Arimo",Arial,sans-serif;padding:0 3px}
.user-login ul{margin:-4px 0 0 20px;font-weight:400;font-size:12.5px}
.user-login ul a{color:var(--link-pale)}
.user-login button{margin-top:12px;width:52px;height:20px;font:12px "Arimo",Arial,sans-serif;border:1px solid #999;border-radius:2px;background:linear-gradient(#fafafa,#ddd)}
.content{position:absolute;left:260px;top:219px;width:607px;height:474px;background:var(--content);border:3px solid var(--frame);border-radius:8px}
.crumb{margin:5px 0 0 19px;font-size:12.5px;font-weight:700}
.crumb a{color:var(--ink)}
.rule{height:2px;background:linear-gradient(#9c948d,#fff)}
.crumb-rule{margin:2px 8px 0 10px}
.content h1{margin:11px 0 0 10px;font-size:20px;color:var(--title)}
.article{margin:26px 22px 0 23px}
.article h3{font-size:16.5px;text-decoration:underline}
.article p{font-size:12.5px;line-height:15.5px;margin:18px 0 16px}
.article h4{font-size:14.5px;text-decoration:underline;margin-top:18px}
.end-rule{position:absolute;left:23px;right:23px;top:447px}
.footer{position:absolute;left:0;right:0;top:718px;text-align:center;font-size:12.5px;font-weight:700}
.footer a{color:var(--ink)}
</style>
</head>
<body>
<div class="backdrop" role="img" aria-label="Chocolate brown background with a hand-drawn fruit and vegetable pattern"></div>
<div class="sheet">
  <nav class="utility"><a href="#">Login</a><span class="sep">|</span><a href="#">Register</a></nav>
  <header class="masthead"><span class="brand-mark"></span><span class="brand-name">Bright Vale</span></header>

  <aside class="box main-menu">
    <h2>Main menu</h2>
    <ul>
      <li><a class="warm" href="#">Home</a></li>
      <li><a class="warm" href="#">About Us</a></li>
      <li><a class="warm" href="#">Nutrition &amp; Diet</a></li>
      <li><a href="#">Paediatric Gastroenterology</a></li>
      <li><a href="#">Fees &amp; Rebate</a></li>
      <li><a href="#">For Doctors</a></li>
      <li><a href="#">Location</a></li>
      <li><a href="#">Contact</a></li>
      <li><a href="#">News &amp; Blog</a></li>
    </ul>
  </aside>

  <main class="content">
    <div class="crumb"><a href="#">Home</a></div>
    <div class="rule crumb-rule"></div>
    <h1>Nutrition &amp; Diet</h1>
    <div class="article">
      <h3>Individual Consultation</h3>
      <p>Sed turpis neque, venenatis condimentum ex sit amet, fermentum ultrices mauris. Curabitur vel ex sem. Pellentesque tincidunt lectus augue, et suscipit est suscipit at. Maecenas ut gravida lorem. Nunc finibus, purus non malesuada lacinia, metus urna malesuada massa, nec interdum augue eros vel neque. Vivamus vitae dolor a mauris sollicitudin posuere quis a lectus. Nunc fringilla quam non massa iaculis, vel imperdiet dui gravida.</p>
      <h3>Group Based Services</h3>
      <p>Maecenas congue vel urna a convallis. Aenean auctor orci at magna ultricies, a tempus purus congue. Suspendisse eget turpis malesuada, blandit nibh ut, faucibus turpis. Suspendisse mattis mi consequat dolor dapibus condimentum. Mauris gravida purus ut tempor congue. Integer lorem enim, vehicula sodales varius at, vestibulum eget tortor. Quisque in massa ultrices, euismod diam in, mattis risus.</p>
      <h3>Downloadable Food Diaries For Recording</h3>
      <h4>Food Diary</h4>
      <h4>Food &amp; Symptom Diary</h4>
    </div>
    <div class="rule end-rule"></div>
  </main>

  <aside class="box user-login">
    <h2>User login</h2>
    <form>
      <label for="user">Username <span class="req">*</span></label>
      <input id="user" type="text" value="Tamsin">
      <label for="pass">Password <span class="req">*</span></label>
      <input id="pass" type="password" value="secretpass1">
      <ul><li><a href="#">Request new password</a></li></ul>
      <button type="button">Log in</button>
    </form>
  </aside>

  <footer class="footer"><a href="#">Bright Vale</a> © Copyright 2014</footer>
</div>
</body>
</html>
```